Display wall/splashback design

We are looking at a design to suit the background display/splashback wall of our instore showroom displays needs to be in suttle colours that do not detract from the appliances attached to this wall.
Most of the rangehoods on display are of a stainless colour hence the background cannot have strong solid colours that will attract the eye of the customer away from the products .
One of the main features of our rangehoods is their silence, so something to highlites silence/quiet would be most appropiate.
Sixe is 1.8 metres in height x 6 metres in length

Target Market(s)

High end consumer, women between 25 and 50

Industry/Entity Type

Retail

Requirements
Must have
• An overall gently/quiet and enviromentally friendly look.
A background that inhances the product displayed upon it.

Should not have
• Strong or dominant images nor strong or dominant colours

```html
<!DOCTYPE html>
<html lang="en">
<head>
<meta charset="utf-8">
<title>Showroom Splashback Wall</title>
<style>
  :root {
    --wall-charcoal: #141311;
    --wall-charcoal-soft: #1b1a17;
    --brass-line: #a8892c;
    --brass-glow: rgba(138, 114, 34, 0.55);
    --brass-haze: rgba(138, 114, 34, 0);
  }
  html, body {
    margin: 0;
    padding: 0;
    width: 1200px;
    height: 444px;
    overflow: hidden;
    background: var(--wall-charcoal);
  }
  .splashback {
    position: relative;
    width: 1200px;
    height: 444px;
    overflow: hidden;
    background: linear-gradient(to bottom, var(--wall-charcoal-soft) 0%, var(--wall-charcoal) 70%);
  }
  .glow-band {
    position: absolute;
    left: 0;
    width: 1200px;
    height: 50px;
    background: linear-gradient(to bottom, var(--brass-haze) 0%, var(--brass-glow) 100%);
    filter: blur(5px);
    -webkit-mask-image: linear-gradient(to right, transparent 0%, #000 1.5%, #000 98.5%, transparent 100%);
    mask-image: linear-gradient(to right, transparent 0%, #000 1.5%, #000 98.5%, transparent 100%);
  }
  .glow-band--upper { top: 286px; }
  .glow-band--lower { top: 355px; }
  .brass-line {
    position: absolute;
    left: 0;
    width: 1200px;
    height: 10px;
    background: var(--brass-line);
  }
  .brass-line--upper { top: 333px; }
  .brass-line--lower { top: 402px; }
</style>
</head>
<body>
  <div class="splashback">
    <div class="glow-band glow-band--upper"></div>
    <div class="brass-line brass-line--upper"></div>
    <div class="glow-band glow-band--lower"></div>
    <div class="brass-line brass-line--lower"></div>
  </div>
</body>
</html>
```